Brivolt Technologies business card design

We need a business card designed with our new logo. it would be great if the card could communicate it is a technology based company.

Target Market(s)

system integrators

Industry/Entity Type

technology, IOT

Contact Information for Business Card

Name, designation, Address, telephone number, email address

Requirements
Must have
• logo and company name
Nice to have
• something to do with technology

```html
<!DOCTYPE html>
<html lang="en">
<head>
<meta charset="utf-8">
<title>Brivolt Technologies – Business Card</title>
<link href="https://fonts.googleapis.com/css2?family=Arimo:wght@400;700&display=swap" rel="stylesheet">
<style>
  :root {
    --backdrop: #d9d9d7;
    --card: #353535;
    --accent: #f7941d;
    --text-light: #f2f2f2;
    --text-muted: #d6d6d6;
  }
  * { margin: 0; padding: 0; box-sizing: border-box; }
  html, body {
    width: 1200px; height: 801px; overflow: hidden;
    background: var(--backdrop);
    font-family: "Arimo", Arial, sans-serif;
  }
  .sheet {
    position: relative; width: 1200px; height: 801px;
    display: flex; align-items: center; justify-content: center; gap: 40px;
  }
  .card {
    position: relative; width: 540px; height: 309px;
    background: var(--card);
    border-bottom: 6px solid var(--accent);
    box-shadow: 0 10px 24px rgba(0,0,0,0.25);
  }
  .card--front { padding: 38px 40px; }
  .brand {
    display: flex; align-items: center; gap: 10px;
    font-weight: 700; text-transform: uppercase;
  }
  .brand__mark { width: 14px; height: 14px; background: var(--accent); flex: none; }
  .card--front .brand__name { font-size: 24px; letter-spacing: 1px; color: var(--text-light); }
  .holder { margin-top: 26px; }
  .holder__name {
    font-size: 19px; font-weight: 700; color: var(--accent);
    text-transform: uppercase; letter-spacing: 0.5px;
  }
  .holder__role { margin-top: 4px; font-size: 14px; color: var(--text-light); }
  .address { margin-top: 16px; font-size: 13px; line-height: 1.35; color: var(--text-muted); }
  .contacts { margin-top: 14px; list-style: none; font-size: 13px; color: var(--text-muted); }
  .contacts li { display: flex; align-items: center; gap: 8px; line-height: 1.5; }
  .contacts svg { width: 11px; height: 11px; flex: none; }
  .card--back { display: flex; align-items: center; justify-content: center; }
  .card--back .brand { gap: 14px; }
  .card--back .brand__mark { width: 20px; height: 20px; }
  .card--back .brand__name { font-size: 30px; letter-spacing: 2px; color: var(--accent); }
</style>
</head>
<body>
<main class="sheet">
  <section class="card card--front" aria-label="Card front">
    <div class="brand">
      <span class="brand__mark"></span>
      <span class="brand__name">Brivolt Technologies</span>
    </div>
    <div class="holder">
      <p class="holder__name">Daniel Harwick</p>
      <p class="holder__role">CEO/Founder</p>
    </div>
    <p class="address">5741 Street Name<br>Country Name AB 8754</p>
    <ul class="contacts">
      <li>
        <svg viewBox="0 0 12 12" aria-hidden="true"><path fill="#f7941d" d="M2.5 1l2 2-1 1.3c.7 1.5 1.7 2.5 3.2 3.2L8 6.5l2 2-1.2 1.8C5 10 2 7 1.7 3.2z"/></svg>
        <span>(123) 555-0184</span>
      </li>
      <li>
        <svg viewBox="0 0 12 12" aria-hidden="true"><rect x="1" y="2.5" width="10" height="7" fill="#f7941d"/><path d="M1 2.5l5 4 5-4" fill="none" stroke="#353535" stroke-width="1"/></svg>
        <span>info@brivolttech.com</span>
      </li>
      <li>
        <svg viewBox="0 0 12 12" aria-hidden="true"><circle cx="6" cy="6" r="5" fill="none" stroke="#f7941d" stroke-width="1.3"/><path d="M1 6h10M6 1c-2.5 3-2.5 7 0 10M6 1c2.5 3 2.5 7 0 10" fill="none" stroke="#f7941d" stroke-width="1"/></svg>
        <span>www.brivolttech.com</span>
      </li>
    </ul>
  </section>

  <section class="card card--back" aria-label="Card back">
    <div class="brand">
      <span class="brand__mark"></span>
      <span class="brand__name">Brivolt Technologies</span>
    </div>
  </section>
</main>
</body>
</html>
```